Whitcombe Business Card Design

The name of the business is Dario Whitcombe, CPA LLC
The service that we offer is Accounting, Tax & Consulting Services. I need it to have the following items:
Dario Whitcombe, Principal
Phone Number
Email Address
Physical Address

I have attached the company logo, one in black and one in white. Please provide a design in black background and the other in white background. Please include "Accounting, Tax & Consulting Services". I want the business card to be clean and very professional.

```html
<!DOCTYPE html>
<html lang="en">
<head>
<meta charset="utf-8">
<title>Whitcombe Business Card Design</title>
<link rel="stylesheet" href="https://fonts.googleapis.com/css2?family=Montserrat:wght@600&family=Roboto:wght@400;500&display=swap">
<style>
  :root {
    --page-bg: #dadada;
    --card-black: #141414;
    --texture-tone: #1c1c1c;
    --panel-white: #edf0f4;
    --ink-dark: #333638;
    --accent-red: #9b1b1e;
    --mark-grey: #5b5b5d;
    --tag-grey: #a7a7a9;
  }
  * { margin: 0; padding: 0; box-sizing: border-box; }
  html, body { width: 1200px; height: 900px; overflow: hidden; }
  body { background: var(--page-bg); position: relative; font-family: "Roboto", Arial, sans-serif; }

  .card {
    position: absolute;
    left: 233px;
    background: var(--card-black);
    box-shadow: 0 3px 10px rgba(0,0,0,0.25);
    overflow: hidden;
  }
  .card-front { top: 43px; width: 700px; height: 398px; }
  .card-back { top: 457px; width: 706px; height: 403px; }

  .texture {
    position: absolute; inset: 0;
    background: radial-gradient(ellipse at center, var(--texture-tone), var(--card-black));
  }

  .brand {
    position: absolute;
    display: flex; align-items: center;
    font-family: "Montserrat", Arial, sans-serif;
    font-weight: 600;
    color: var(--mark-grey);
    white-space: nowrap;
  }
  .brand-square { background: var(--mark-grey); flex: none; }

  .card-front .brand { left: 0; right: 0; top: 170px; justify-content: center; gap: 18px; font-size: 33px; }
  .card-front .brand-square { width: 40px; height: 40px; }

  .card-back .brand { left: 440px; top: 215px; gap: 10px; font-size: 16px; color: var(--tag-grey); }
  .card-back .brand-square { width: 18px; height: 18px; background: var(--tag-grey); }

  .contact-panel { position: absolute; left: 0; top: 0; width: 450px; height: 340px; }

  .person { position: absolute; left: 47px; top: 48px; }
  .person-name { font-size: 31px; font-weight: 500; color: var(--ink-dark); line-height: 1.1; }
  .person-role { font-size: 19px; color: var(--accent-red); margin-top: 2px; margin-left: -1px; }

  .address { position: absolute; left: 41px; top: 146px; font-size: 20.5px; line-height: 27px; color: var(--ink-dark); }

  .contact-line { position: absolute; left: 41px; display: flex; align-items: center; font-size: 21px; color: var(--ink-dark); }
  .contact-line svg { width: 18px; height: 18px; margin-right: 22px; fill: var(--accent-red); }
  .line-phone { top: 218px; }
  .line-email { top: 263px; }

  .services {
    position: absolute; left: 0; right: 0; top: 360px;
    text-align: center;
    font-family: "Roboto", Arial, sans-serif; font-weight: 500;
    font-size: 20px; letter-spacing: 7.4px;
    color: var(--tag-grey);
  }
</style>
</head>
<body>

<section class="card card-front">
  <div class="texture" role="img" aria-label="Subtle dark repeating texture"></div>
  <div class="brand"><span class="brand-square"></span>Dario Whitcombe, CPA LLC</div>
</section>

<section class="card card-back">
  <div class="texture" role="img" aria-label="Subtle dark repeating texture"></div>
  <svg class="contact-panel" viewBox="0 0 450 340" aria-hidden="true">
    <polygon points="0,0 347,0 450,340 34,340 0,305" fill="var(--panel-white)"/>
  </svg>

  <div class="person">
    <p class="person-name">Dario Whitcombe</p>
    <p class="person-role">Principal</p>
  </div>

  <p class="address">421, Address line goes here<br>45552, Country Name</p>

  <p class="contact-line line-phone">
    <svg viewBox="0 0 24 24" aria-hidden="true"><path d="M6.6 10.8a15.1 15.1 0 0 0 6.6 6.6l2.2-2.2a1 1 0 0 1 1-.25 11.4 11.4 0 0 0 3.6.57 1 1 0 0 1 1 1V20a1 1 0 0 1-1 1A17 17 0 0 1 3 4a1 1 0 0 1 1-1h3.5a1 1 0 0 1 1 1c0 1.25.2 2.45.57 3.57a1 1 0 0 1-.25 1z"/></svg>
    (555) 214-0387
  </p>
  <p class="contact-line line-email">
    <svg viewBox="0 0 24 24" aria-hidden="true"><path d="M2 5h20v14H2z M3.5 6.5 12 13l8.5-6.5" stroke="var(--panel-white)" stroke-width="1.6"/></svg>
    info@whitcombe.com
  </p>

  <div class="brand"><span class="brand-square"></span>Dario Whitcombe, CPA LLC</div>

  <p class="services">ACCOUNTING, TAX &amp; CONSULTING SERVICES</p>
</section>

</body>
</html>
```